Vantor Ridge needs a Business Card Design

We need a business card design for an Information Technology company based in Fairfax Virginia called Vantor Ridge. We want the business card to use our logo colors. We need it to be double-sided. The business card needs to look professional but we would like it to be unique. You can get company information from our web site (http://www.vantorridgellc.example).

Target Market(s)

Target market is Government Agencies and Business Professionals.

Industry/Entity Type

Business

Requirements
Must have
• Must have section for company name, company address, company URL, employee name, title, phone and email. Also must have company logo and space for entering logos.

```html
<!DOCTYPE html>
<html lang="en">
<head>
<meta charset="utf-8">
<title>Vantor Ridge – Business Card, Front and Back</title>
<link rel="stylesheet" href="https://fonts.googleapis.com/css2?family=Open+Sans:wght@400;600;700&display=swap">
<style>
  :root {
    --navy: #26338f;
    --blue: #0a76be;
    --white: #ffffff;
    --ink: #4a4a4a;
    --page: #e9e7e3;
  }
  * { box-sizing: border-box; margin: 0; padding: 0; }
  html, body { width: 1200px; height: 1024px; overflow: hidden; }
  body {
    background: var(--page);
    font-family: "Open Sans", Arial, sans-serif;
    display: flex;
    flex-direction: column;
    align-items: center;
    justify-content: center;
    gap: 40px;
  }
  .card {
    position: relative;
    width: 780px;
    height: 446px;
    background: var(--white);
    overflow: hidden;
    box-shadow: 0 6px 18px rgba(0,0,0,.18);
  }

  /* Front */
  .front .edge-navy { position: absolute; right: 0; top: 150px; width: 50px; height: 296px; background: var(--navy); }
  .front .edge-blue { position: absolute; right: 0; top: 0; width: 50px; height: 134px; background: var(--blue); }
  .front .wordmark {
    position: absolute; left: 48px; top: 72px;
    color: var(--navy); font-weight: 700; font-size: 34px; line-height: 40px;
  }
  .front .person { position: absolute; left: 108px; top: 170px; }
  .person .name { color: var(--navy); font-weight: 700; font-size: 19px; }
  .person .title { color: var(--blue); font-size: 17px; margin-top: 2px; }
  .contact { position: absolute; left: 108px; top: 248px; list-style: none; color: var(--ink); font-size: 17px; line-height: 24px; }
  .contact li { display: flex; align-items: flex-start; gap: 10px; }
  .contact .icon { width: 16px; height: 16px; margin-top: 4px; flex: none; fill: var(--blue); }
  .contact .gap { margin-top: 8px; }

  /* Back */
  .back .top-band { position: absolute; left: 0; top: 0; width: 780px; height: 170px; background: var(--blue); }
  .back .top-rule { position: absolute; left: 0; top: 170px; width: 780px; height: 14px; background: var(--navy); }
  .back .wordmark {
    position: absolute; right: 60px; top: 262px;
    color: var(--navy); font-weight: 700; font-size: 44px; line-height: 52px;
  }
  .back .url-band {
    position: absolute; left: 0; bottom: 0; width: 780px; height: 52px; background: var(--blue);
    color: var(--white); font-size: 17px; display: flex; align-items: center; padding-left: 40px;
  }
</style>
</head>
<body>

  <section class="card front" aria-label="Card front">
    <div class="edge-blue"></div>
    <div class="edge-navy"></div>

    <p class="wordmark">Vantor Ridge</p>

    <div class="person">
      <p class="name">Dana Whitfield</p>
      <p class="title">Job Title</p>
    </div>

    <ul class="contact">
      <li>
        <svg class="icon" viewBox="0 0 16 16"><path d="M8 1 1 8h2v7h4v-4h2v4h4V8h2z"/></svg>
        <span>1480 Harlow Ave, Suite 300<br>Fairfax, VA 22030</span>
      </li>
      <li class="gap">
        <svg class="icon" viewBox="0 0 16 16"><path d="M4 1 6.5 4 5 6c1 2 3 4 5 5l2-1.5 3 2.5-2 3C7 15 1 9 1 3z"/></svg>
        <span>555.014.2290</span>
      </li>
      <li>
        <svg class="icon" viewBox="0 0 16 16"><rect x="2" y="3" width="12" height="10" rx="1"/></svg>
        <span>555.014.7735</span>
      </li>
      <li>
        <svg class="icon" viewBox="0 0 16 16"><path d="M1 3h14v10H1z M1 3l7 6 7-6" stroke="#fff" stroke-width="1"/></svg>
        <span>name@vantorridgellc.example</span>
      </li>
      <li>
        <svg class="icon" viewBox="0 0 16 16"><circle cx="8" cy="8" r="7"/><path d="M1 8h14M8 1c-3 4-3 10 0 14M8 1c3 4 3 10 0 14" stroke="#fff" fill="none"/></svg>
        <span>www.vantorridgellc.example</span>
      </li>
    </ul>
  </section>

  <section class="card back" aria-label="Card back">
    <div class="top-band"></div>
    <div class="top-rule"></div>
    <p class="wordmark">Vantor Ridge</p>
    <p class="url-band">www.vantorridgellc.example</p>
  </section>

</body>
</html>
```